Book Cover on Entrepreneurship for Eye Doctors

Book Title: The Lens Practice Builder: How to launch with confidence
Author: Rufus Tembley, Optom, MBA, DBA, EIC
I need a Book Cover with the following descriptions:
Topic: the book topic is entrepreneurship knowledge for eye care professionals.
The book's audience: eye care professionals who you know as Opticians, who sell eyeglasses and sunglasses;
Optometrists, test eyes, fit contact lenses, and prescribe medication
Ophthalmologists, perform eye surgery
More about the audience:
1- Young eye care professionals who don’t know about entrepreneurship and those who are stuck in the 9-to-5 job;
2- This is the first book written on entrepreneurship with eye care professionals in mind.
3- Private practice owners the established business guys who are looking to grow their business;
4- Many eye care professionals are MBA holders they may have learned a little bit about entrepreneurship during their MBA studies.
Use the sample cover above and the suggestions that follow as a guide:
1- The cover should be very simple leaving an empty space somewhere to sign the book;
2- The Title and author name should use a modern font;
3- The cover should provide info about what's inside the book through illustrations, for example:
a- Gears: illustrating entrepreneur growth mindset (or anything more explicit)
b- Spectacles, sunglasses, lenses, eye drops, or any other eye care-related correction tools illustrating eye care (or anything more explicit)
c- Symbols illustrating ideas, opportunity, and profit, like money, charts, light bulbs, brain, and coins,...(or anything more explicit)
d- Entrepreneurship illustrated by Briefcase, tie, suit,... (or anything more explicit)

The rest is your creativity and imagination interplay.

Target Market(s)

Eye care professionals: Opticians, Optometrists, Ophthalmologists, Eye Care Administrators, Students in eye specialties.

Industry/Entity Type

eye care

Requirements
Must have
• 1- The cover should be very simple leaving an empty space somewhere to sign the book; 2- The Title and author name should use a modern font; 3- The cover should provide info about what's inside the book through illustrations, for example: a- Gears: illustrating entrepreneur growth mindset (or anything more explicit) b- Spectacles, sunglasses, lenses, eye drops, or any other eye care-related correction tools illustrating eye care (or anything more explicit) c- Symbols illustrating ideas, opportunity, and profit, like money, charts, light bulbs, brain, and coins,...(or anything more explicit) d- Entrepreneurship illustrated by Briefcase, tie, suit,... (or anything more explicit)

```html
<!DOCTYPE html>
<html lang="en">
<head>
<meta charset="utf-8">
<title>The Lens Practice Builder — Book Cover</title>
<link rel="stylesheet" href="https://fonts.googleapis.com/css2?family=Bebas+Neue&family=Montserrat:wght@400&display=swap">
<style>
  :root {
    --back-blue: #173f6f;
    --deep-navy: #0c2440;
    --cyan: #0ea5c8;
    --front-mist: #e8f3f3;
    --body-blue: #7fb4d8;
    --portrait-grey: #8aa0b8;
    --white: #ffffff;
  }
  * { margin: 0; padding: 0; box-sizing: border-box; }
  html, body { width: 1200px; height: 968px; overflow: hidden; background: var(--white); }
  .canvas { position: relative; width: 1200px; height: 968px; }
  .wrap { position: absolute; left: 76px; top: 121px; width: 1050px; height: 727px; }

  .back-cover { position: absolute; left: 0; top: 0; width: 484px; height: 727px; background: var(--back-blue); }
  .spine { position: absolute; left: 484px; top: 0; width: 82px; height: 727px; background: var(--back-blue); border-left: 1px solid #3c6190; }
  .front-cover { position: absolute; left: 566px; top: 0; width: 484px; height: 727px; background: var(--front-mist); }

  .title-svg { position: absolute; overflow: visible; }
  .title-svg text { font-family: "Bebas Neue", sans-serif; }

  .back-blurb {
    position: absolute; left: 35px; top: 206px; width: 414px;
    font-family: "Montserrat", sans-serif; font-size: 10px; line-height: 12.1px;
    color: var(--body-blue); text-align: justify;
  }
  .back-author {
    position: absolute; left: 0; top: 425px; width: 484px; text-align: center;
    font-family: "Bebas Neue", sans-serif; font-size: 15px; letter-spacing: 2.6px; color: var(--white);
  }
  .author-portrait { position: absolute; left: 37px; top: 460px; width: 116px; height: 151px; background: var(--portrait-grey); }
  .author-bio {
    position: absolute; left: 162px; top: 459px; width: 287px;
    font-family: "Montserrat", sans-serif; font-size: 10px; line-height: 12.1px;
    color: var(--body-blue); text-align: justify;
  }

  .cover-visual {
    position: absolute; left: 0; top: 0; width: 484px; height: 285px;
    background: linear-gradient(180deg, #1d3a55 0%, #2c5f86 35%, #6fa4c0 65%, #b9d8e0 85%, var(--front-mist) 100%);
  }
  .tagline-rule { position: absolute; left: 105px; width: 280px; height: 1px; background: var(--cyan); }
  .tagline {
    position: absolute; left: 0; top: 613px; width: 484px; text-align: center;
    font-family: "Bebas Neue", sans-serif; font-size: 23px; letter-spacing: 1.4px; color: var(--deep-navy);
  }
  .author-band {
    position: absolute; left: 0; top: 665px; width: 484px; height: 62px; background: var(--deep-navy);
    display: flex; align-items: center; justify-content: center;
    font-family: "Bebas Neue", sans-serif; font-size: 33px; letter-spacing: 1.2px; color: var(--white);
  }
</style>
</head>
<body>
<div class="canvas">
  <div class="wrap">

    <section class="back-cover">
      <svg class="title-svg" style="left:0;top:0" width="484" height="200" viewBox="0 0 484 200">
        <text x="137" y="91" font-size="82" fill="#fff" textLength="209" lengthAdjust="spacingAndGlyphs">THE LENS</text>
        <text x="137" y="154" font-size="82" fill="#fff" textLength="209" lengthAdjust="spacingAndGlyphs">PRACTICE</text>
        <text x="137" y="188" font-size="42" fill="#0ea5c8" textLength="209" lengthAdjust="spacing">BUILDER</text>
      </svg>
      <div class="back-blurb">
        <p>Lorem ipsum dolor sit amet, consectetuer adipiscing elit, sed diam nonummy nibh euismod tincidunt ut laoreet dolore magna aliquam erat volutpat. Ut wisi enim ad minim veniam, quis nostrud exerci tation ullamcorper suscipit lobortis nisl ut aliquip ex ea commodo consequat. Duis autem vel eum iriure dolor in hendrerit in vulputate velit esse molestie consequat, vel illum dolore eu feugiat nulla facilisis at vero eros et accumsan et iusto odio dignissim qui blandit praesent luptatum zzril delenit augue duis dolore te feugait nulla facilisi.</p>
        <p>Lorem ipsum dolor sit amet, cons ectetuer adipiscing elit, sed diam nonummy nibh euismod tincidunt ut laoreet dolore magna aliquam erat volutpat. Ut wisi enim ad minim veniam, quis nostrud exerci tation ullamcorper suscipit lobortis nisl ut aliquip ex ea commodo consequat.</p>
        <p>Lorem ipsum dolor sit amet, consectetuer adipiscing elit, sed diam nonummy nibh euismod tincidunt ut laoreet dolore magna aliquam erat volutpat. Ut wisi enim ad minim veniam, quis nostrud exerci tation ullamcorper suscipit lobortis nisl ut aliquip ex ea commodo consequat. Duis autem vel eum iriure dolor in hendrerit in vulputate velit esse molestie consequat, vel illum dolore eu feugiat nulla facilisis at</p>
      </div>
      <div class="back-author">RUFUS TEMBLEY, OPTOM, MBA, DBA, EIC</div>
      <div class="author-portrait" role="img" aria-label="Author portrait placeholder"></div>
      <div class="author-bio">
        <p>Lorem ipsum dolor sit amet, consectetuer adipiscing elit, sed diam nonummy nibh euismod tincidunt ut laoreet dolore magna aliquam erat volutpat. Ut wisi enim ad minim veniam, quis nostrud exerci tation ullamcorper suscipit lobortis nisl ut aliquip ex ea commodo consequat. Duis autem vel eum iriure dolor in hendrerit in vulputate velit esse molestie consequat, vel illum dolore eu feugiat nulla facilisis at vero eros et accumsan et iusto odio dignissim qui blandit praesent luptatum zzril delenit augue duis dolore te feugait nulla facilisi.</p>
        <p>Lorem ipsum dolor sit amet, cons ectetuer adipiscing elit, sed diam nonummy nibh euismod tincidunt ut laoreet dolore magna aliquam erat volutpat. Ut wisi enim ad</p>
      </div>
    </section>

    <section class="spine">
      <svg class="title-svg" style="left:0;top:0" width="82" height="727" viewBox="0 0 82 727">
        <g transform="translate(52 648) rotate(-90)">
          <text x="0" y="0" font-size="32"><tspan fill="#fff">THE LENS PRACTICE </tspan><tspan fill="#0ea5c8">BUILDER</tspan></text>
        </g>
        <g transform="translate(49 340) rotate(-90)">
          <text x="0" y="0" font-size="21" fill="#fff" letter-spacing="2.4">RUFUS TEMBLEY, OPTOM, MBA, DBA, EIC</text>
        </g>
      </svg>
    </section>

    <section class="front-cover">
      <div class="cover-visual" role="img" aria-label="Photo of a professional's hands at a desk with floating business charts, gears, eyeglasses, eye and briefcase icons"></div>
      <svg class="title-svg" style="left:0;top:0" width="484" height="600" viewBox="0 0 484 600">
        <text x="34" y="404" font-size="157" fill="#0c2440" textLength="396" lengthAdjust="spacingAndGlyphs">THE LENS</text>
        <text x="34" y="524" font-size="162" fill="#0c2440" textLength="396" lengthAdjust="spacingAndGlyphs">PRACTICE</text>
        <text x="34" y="591" font-size="83" fill="#0ea5c8" textLength="396" lengthAdjust="spacing">BUILDER</text>
      </svg>
      <div class="tagline-rule" style="top:610px"></div>
      <div class="tagline">HOW TO LAUNCH WITH CONFIDENCE</div>
      <div class="tagline-rule" style="top:641px"></div>
      <div class="author-band">RUFUS TEMBLEY, OPTOM, MBA, DBA, EIC</div>
    </section>

  </div>
</div>
</body>
</html>
```